Business card for denture clinic Veltrimora

We need a new business card with our new logo. We are a denture clinic in New Zealand with our target market being 45+ years old. We would need a space on the back to write our patients next appointment on. We would space for only one appointment rather than a list. We will attach a photo showing an example of this. But of course, we would like to see your twist on this. We want it to be bold and easy to read and a good mixture of professional but modern. We have attached our logo to be used on the card.

Target Market(s)

People aged 45+ needing dentures

Industry/Entity Type

Dental

Contact Information for Business Card

We want our logo on the front and the space to write an appointment on the back. I've attached an example our our old business card showing this. We need to have the technicians details on the front.

Font styles to use
Sans Serif

Colors
0255a3
919191
fbfbfb

Requirements
Must have
• The following details:
• Liam Dorsett BDT, PGDipCDentTech Calverin
• Dental Prosthetist
• Phone numbers: 0800 47 3125
• 09 572 1394
• Email: liam@veltrimora.co.nz
• www.veltrimora.co.nz
• Address: 14 Marlow Crest Road
• Halbrook West
• Auckland 0793
Nice to have
• We would like our business cards to have more than just two colours as we want them to be more vibrant. We have uploaded an example of a business card we liked that showed this.

```html
<!DOCTYPE html>
<html lang="en">
<head>
<meta charset="UTF-8">
<title>Veltrimora – Business Card</title>
<link href="https://fonts.googleapis.com/css2?family=Chakra+Petch:wght@400;500;600;700&display=swap" rel="stylesheet">
<style>
  :root {
    --brand-blue: #0255a3;
    --card-blue: #0270bb;
    --ink: #4a4a4a;
    --grey: #919191;
    --paper: #fbfbfb;
    --stage: #333333;
    --white: #ffffff;
  }
  * { margin: 0; padding: 0; box-sizing: border-box; }
  html, body {
    width: 1200px; height: 900px; overflow: hidden;
    background: var(--stage);
    font-family: "Chakra Petch", sans-serif;
  }
  .stage { position: relative; width: 1200px; height: 900px; }
  .card {
    position: absolute; top: 271px; width: 457px; height: 281px;
    border-radius: 14px; overflow: hidden;
    box-shadow: 3px 4px 6px rgba(0,0,0,0.55);
  }
  /* Front */
  .card-front { left: 137px; background: var(--paper); }
  .front-band {
    position: absolute; left: 360px; top: 0; width: 97px; height: 100%;
    background: var(--card-blue);
  }
  .brand { position: absolute; left: 28px; top: 28px; text-align: center; }
  .brand-name {
    font-size: 22px; font-weight: 600; color: var(--brand-blue);
    letter-spacing: 2.5px; line-height: 1;
  }
  .brand-tagline {
    font-size: 9.5px; color: var(--grey); letter-spacing: 2px; margin-top: 3px;
  }
  .brand-square {
    position: absolute; left: 308px; top: 31px; width: 112px; height: 116px;
    background: var(--white); padding: 10px 12px 10px 2px;
    box-shadow: 1px 2px 3px rgba(0,0,0,0.25);
  }
  .brand-square span {
    display: block; width: 100%; height: 100%; background: var(--card-blue);
    border-radius: 3px;
  }
  .address {
    position: absolute; left: 28px; top: 77px;
    font-size: 13.5px; line-height: 17px; color: var(--ink);
  }
  .person { position: absolute; left: 28px; top: 145px; white-space: nowrap; }
  .person-name {
    font-size: 19px; font-weight: 700; color: var(--brand-blue);
    letter-spacing: 0.5px; line-height: 1;
  }
  .person-credentials {
    font-size: 12px; font-weight: 500; margin-left: 2px; letter-spacing: 0;
  }
  .person-role {
    font-size: 15px; font-weight: 600; color: var(--ink); margin-top: 3px;
  }
  .contacts { position: absolute; left: 28px; top: 194px; list-style: none; }
  .contacts li {
    display: flex; align-items: center; gap: 9px;
    font-size: 13.5px; color: var(--ink); height: 20.5px;
  }
  .contacts svg { width: 11px; height: 11px; flex: none; }
  /* Back */
  .card-back { left: 626px; background: var(--card-blue); }
  .back-square {
    position: absolute; left: 196px; top: 49px; width: 66px; height: 66px;
    border: 1px solid rgba(255,255,255,0.55); border-radius: 2px;
    background: var(--card-blue);
    box-shadow: 1px 2px 3px rgba(0,0,0,0.3);
  }
  .appointment-title {
    position: absolute; left: 0; right: 0; top: 170px; text-align: center;
    font-size: 17px; font-weight: 600; color: var(--white);
  }
  .appointment-fields {
    position: absolute; left: 80px; top: 215px;
    display: flex; align-items: center; color: var(--white);
    font-size: 15px; font-weight: 500;
  }
  .field-label { margin-right: 7px; }
  .field-box {
    width: 99px; height: 22px; background: var(--white); border-radius: 3px;
    margin-right: 17px;
  }
</style>
</head>
<body>
<main class="stage">
  <section class="card card-front" aria-label="Business card front">
    <div class="front-band"></div>
    <div class="brand">
      <div class="brand-name">VELTRIMORA</div>
      <div class="brand-tagline">THE DENTURE EXPERTS</div>
    </div>
    <div class="brand-square"><span></span></div>
    <p class="address">14 Marlow Crest Road<br>Halbrook West Auckland 0793</p>
    <div class="person">
      <div class="person-name">LIAM DORSETT <span class="person-credentials">BDT, PG Dip Dent Tech Calverin</span></div>
      <div class="person-role">Dental Prosthetist</div>
    </div>
    <ul class="contacts">
      <li>
        <svg viewBox="0 0 11 11"><rect width="11" height="11" fill="#0255a3"/><path d="M3 3.2h5v1.2H3z M3.6 5h3.8v3H3.6z" fill="#fff"/></svg>
        0800 47 3125
      </li>
      <li>
        <svg viewBox="0 0 11 11"><rect width="11" height="11" fill="#0255a3"/><path d="M3 3.2h5v1.2H3z M3.6 5h3.8v3H3.6z" fill="#fff"/></svg>
        09 572 1394
      </li>
      <li>
        <svg viewBox="0 0 11 11"><rect width="11" height="11" fill="#0255a3"/><rect x="2.5" y="3.5" width="6" height="4" fill="#fff"/><path d="M2.5 3.5l3 2.2 3-2.2" stroke="#0255a3" stroke-width="0.7" fill="none"/></svg>
        liam@veltrimora.co.nz
      </li>
    </ul>
  </section>

  <section class="card card-back" aria-label="Business card back">
    <div class="back-square"></div>
    <h2 class="appointment-title">Your next appointment</h2>
    <div class="appointment-fields">
      <span class="field-label">Date</span><span class="field-box"></span>
      <span class="field-label">Time</span><span class="field-box"></span>
    </div>
  </section>
</main>
</body>
</html>
```